Elevating our current Business Card Design

We want to elevate our current business card with a new design to look like a zenith 300 company. We are a premium lubricant distributor (oil and grease).
We need 2 versions, version 1 is as per the uploaded a copy of our current business card with the English version.
For our Chinese version we need to use the front to be English in English and have the back of the card designed exactly like the front for all info to be in Chinese.
The design template needs to be such that we can amend the template with adding different information for each person's card.
The background colour of the card can be changed- we just need to clearly see all information on the card and logos.
The QJR and Ember steady logos cannot have any colour or display changes- only use the logos attached.
All logos need to be included and all information from the attached current card

```html
<!DOCTYPE html>
<html lang="en">
<head>
<meta charset="utf-8">
<title>Norvane Business Card</title>
<link href="https://fonts.googleapis.com/css2?family=Open+Sans:wght@400;600;700;800&display=swap" rel="stylesheet">
<style>
  :root {
    --stage: #222222;
    --brand-red: #ec2b33;
    --deep-red: #a3161d;
    --forest: #05311f;
    --orange: #f08a1c;
    --gold: #d9a22b;
    --ink: #1a1a1a;
    --white: #ffffff;
    --silver: #9a9ca0;
  }
  * { box-sizing: border-box; margin: 0; padding: 0; }
  html, body { width: 1200px; height: 780px; overflow: hidden; }
  body {
    background: var(--stage);
    font-family: "Open Sans", Arial, sans-serif;
    position: relative;
  }
  .card {
    position: absolute;
    top: 230px;
    width: 540px;
    height: 320px;
    border-radius: 16px;
    overflow: hidden;
  }
  .card-back { left: 40px; background: var(--brand-red); }
  .card-front { left: 620px; background: var(--white); }

  .back-pattern {
    position: absolute; inset: 0;
    background: linear-gradient(135deg, #ee323a, #e0262e);
  }
  .back-wordmark {
    position: absolute; right: 34px; top: 132px;
    display: flex; align-items: center; gap: 8px;
    color: var(--white); font-weight: 800; font-size: 30px; letter-spacing: 1px;
  }
  .wordmark-dot { width: 12px; height: 12px; border-radius: 50%; background: var(--white); }

  .front-art { position: absolute; inset: 0; }
  .holder { position: absolute; left: 26px; top: 26px; }
  .holder-name { color: var(--brand-red); font-weight: 800; font-size: 28px; line-height: 1.05; }
  .holder-role { color: var(--ink); font-weight: 600; font-size: 14px; margin-top: 2px; }

  .front-wordmark {
    position: absolute; right: 40px; top: 46px;
    display: flex; align-items: center; gap: 10px;
    color: var(--brand-red); font-weight: 800; font-size: 40px; letter-spacing: 1px;
  }
  .front-wordmark .wordmark-dot { width: 22px; height: 22px; background: var(--gold); }

  .contact { position: absolute; left: 42px; top: 186px; color: var(--white); font-size: 12.5px; line-height: 16px; }
  .contact-address { margin-bottom: 8px; }
  .contact-list { list-style: none; }
  .contact-list li { display: flex; align-items: center; gap: 8px; }
  .contact-list svg { width: 11px; height: 11px; flex: none; }

  .credentials { position: absolute; right: 16px; bottom: 14px; width: 220px; height: 100px; }
  .cert-row { position: absolute; right: 6px; top: 0; display: flex; gap: 10px; }
  .cert-badge { width: 32px; height: 32px; border-radius: 50%; background: var(--orange); border: 3px solid var(--silver); }
  .member-badge { position: absolute; left: 0; top: 30px; width: 54px; height: 28px; border-radius: 14px 14px 4px 4px; background: var(--white); opacity: .9; }
  .partner-strip { position: absolute; left: 6px; right: 0; bottom: 0; height: 34px; display: flex; border: 2px solid var(--brand-red); border-radius: 3px; }
  .strip-name { flex: 1; background: var(--white); display: flex; align-items: center; justify-content: center; color: var(--brand-red); font-weight: 800; font-size: 15px; }
  .strip-partner { width: 84px; background: var(--brand-red); }
</style>
</head>
<body>

  <section class="card card-back" aria-label="Card back">
    <div class="back-pattern" role="img" aria-label="Red background with repeating embossed brand symbol pattern"></div>
    <div class="back-wordmark"><span class="wordmark-dot"></span>NORVANE</div>
  </section>

  <section class="card card-front" aria-label="Card front">
    <svg class="front-art" viewBox="0 0 540 320" preserveAspectRatio="none" aria-hidden="true">
      <path d="M0,172 C130,140 280,150 400,138 C470,130 515,100 540,62 L540,320 L0,320 Z" fill="var(--forest)"/>
      <path d="M0,172 C130,140 280,150 400,138 C470,130 515,100 540,62" fill="none" stroke="var(--deep-red)" stroke-width="7"/>
      <path d="M0,163 C90,130 180,122 250,120" fill="none" stroke="var(--orange)" stroke-width="4"/>
      <path d="M360,126 C440,122 500,96 530,58" fill="none" stroke="var(--gold)" stroke-width="3"/>
    </svg>

    <div class="holder">
      <h1 class="holder-name">Mara Quinlan</h1>
      <p class="holder-role">Administration Executive</p>
    </div>

    <div class="front-wordmark"><span class="wordmark-dot"></span>NORVANE</div>

    <div class="contact">
      <p class="contact-address">48 Freightway Drive<br>Brookdale, WA 6112</p>
      <ul class="contact-list">
        <li><svg viewBox="0 0 12 12"><path d="M2 1 L4.5 1 L5.5 3.5 L4 4.5 C4.6 6 6 7.4 7.5 8 L8.5 6.5 L11 7.5 L11 10 C6 10.5 1.5 6 2 1Z" fill="var(--brand-red)"/></svg>1300 000 417</li>
        <li><svg viewBox="0 0 12 12"><rect x="3" y="0.5" width="6" height="11" rx="1" fill="none" stroke="var(--brand-red)" stroke-width="1.2"/></svg>+61 400 123 456</li>
        <li><svg viewBox="0 0 12 12"><rect x="1" y="4" width="10" height="7" rx="1" fill="var(--brand-red)"/><rect x="3" y="1" width="6" height="4" fill="none" stroke="var(--brand-red)"/></svg>+61 8 9000 4321</li>
        <li><svg viewBox="0 0 12 12"><circle cx="6" cy="6" r="5" fill="var(--brand-red)"/><path d="M1 6 H11 M6 1 C3 4 3 8 6 11 C9 8 9 4 6 1" fill="none" stroke="var(--forest)" stroke-width=".8"/></svg>www.norvanelube.com</li>
        <li><svg viewBox="0 0 12 12"><rect x="0.5" y="2.5" width="11" height="8" rx="1" fill="var(--brand-red)"/><path d="M0.5 3 L6 7 L11.5 3" fill="none" stroke="var(--forest)" stroke-width=".9"/></svg>mara.quinlan@norvanelube.com</li>
      </ul>
    </div>

    <div class="credentials">
      <div class="cert-row">
        <span class="cert-badge" role="img" aria-label="QJR certification badge"></span>
        <span class="cert-badge" role="img" aria-label="QJR certification badge"></span>
        <span class="cert-badge" role="img" aria-label="QJR certification badge"></span>
      </div>
      <span class="member-badge" role="img" aria-label="Ember steady network member badge"></span>
      <div class="partner-strip">
        <span class="strip-name">Norvane</span>
        <span class="strip-partner" role="img" aria-label="Premium lubricants partner badge"></span>
      </div>
    </div>
  </section>

</body>
</html>
```